Lumavento business card

We need a modern business card - With our 4 colors - See web: www.lumavento.dk

I have attached logo and som old business Cards we have - Lets Make the new ones shine...:-) -

Industry/Entity Type

Business

Requirements
Must have
• the logo with lumavento only,

```html
<!DOCTYPE html>
<html lang="da">
<head>
<meta charset="utf-8">
<title>Lumavento – visitkort</title>
<link href="https://fonts.googleapis.com/css2?family=Source+Sans+3:wght@300;400;600&display=swap" rel="stylesheet">
<style>
  :root {
    --purple: #6d2a7f;
    --pink: #e5097f;
    --green: #a3c83a;
    --orange: #f0821e;
    --ink: #3a3a3a;
    --paper: #ffffff;
    --backdrop: #3b3431;
  }
  * { margin: 0; padding: 0; box-sizing: border-box; }
  html, body {
    width: 1200px; height: 844px; overflow: hidden;
    background: var(--backdrop);
    font-family: "Source Sans 3", Arial, sans-serif;
  }
  .card {
    position: absolute; top: 247px;
    width: 540px; height: 350px;
    background: var(--paper);
    overflow: hidden;
    box-shadow: 0 10px 30px rgba(0,0,0,.45);
  }
  .card--front { left: 40px; }
  .card--back { left: 620px; }
  .card__bands { position: absolute; inset: 0; width: 540px; height: 350px; }

  /* front */
  .brand-mark {
    position: absolute; left: 58px; top: 150px;
    display: flex; align-items: center; gap: 10px;
    color: var(--green); font-weight: 400; font-size: 30px;
    letter-spacing: 1px;
  }
  .brand-mark__dot { width: 16px; height: 16px; border-radius: 50%; background: var(--green); }
  .contact { position: absolute; left: 300px; top: 72px; color: var(--green); }
  .contact__name { font-size: 23px; font-weight: 600; line-height: 1; }
  .contact__first { color: var(--pink); }
  .contact__last { color: var(--orange); }
  .contact__title { font-size: 15px; margin-top: 4px; }
  .contact__address { font-size: 15px; line-height: 1.25; margin-top: 20px; }
  .contact__lines { list-style: none; margin-top: 14px; font-size: 15px; line-height: 1.45; }
  .contact__lines li { display: flex; align-items: center; gap: 9px; }
  .contact__lines svg { width: 12px; height: 12px; flex: none; }

  /* back */
  .back-brand {
    position: absolute; left: 0; right: 0; top: 130px;
    text-align: center;
  }
  .back-brand__name {
    display: inline-flex; align-items: center; gap: 12px;
    font-size: 34px; font-weight: 300; letter-spacing: 6px; color: var(--ink);
  }
  .back-brand__dot { width: 14px; height: 14px; border-radius: 50%; background: var(--green); }
  .back-brand__rule { height: 3px; background: var(--green); width: 250px; margin: 14px auto 12px; }
  .back-brand__tagline { font-size: 17px; color: var(--ink); }
</style>
</head>
<body>

<section class="card card--front" aria-label="Visitkort forside">
  <svg class="card__bands" viewBox="0 0 540 350" aria-hidden="true">
    <polygon points="0,0 232,0 222,22 0,22" fill="var(--purple)"/>
    <polygon points="242,0 540,0 540,22 232,22" fill="var(--pink)"/>
    <polygon points="0,326 330,326 340,310 340,350 0,350" fill="var(--green)"/>
    <polygon points="348,310 540,310 540,350 340,350" fill="var(--orange)"/>
  </svg>

  <div class="brand-mark"><span class="brand-mark__dot"></span>lumavento</div>

  <div class="contact">
    <p class="contact__name"><span class="contact__first">Maren</span> <span class="contact__last">Holmgaard</span></p>
    <p class="contact__title">Salgsdirektør</p>
    <p class="contact__address">Solsikkevej 14 - 4690<br>Lyngstrup - Tlf. 31 42 67 80</p>
    <ul class="contact__lines">
      <li><svg viewBox="0 0 12 12"><path d="M2 1l2 0 1 3-1.5 1a6 6 0 0 0 3.5 3.5L8 7l3 1v2a1 1 0 0 1-1 1A9 9 0 0 1 1 2a1 1 0 0 1 1-1z" fill="var(--pink)"/></svg>+45 61 72 83 94</li>
      <li><svg viewBox="0 0 12 12"><rect x="0.5" y="2" width="11" height="8" fill="var(--orange)"/><path d="M0.5 2l5.5 4.5L11.5 2" stroke="#fff" fill="none"/></svg>mh@lumavento.dk</li>
      <li><svg viewBox="0 0 12 12"><circle cx="6" cy="6" r="5.5" fill="var(--purple)"/><circle cx="6" cy="6" r="2" fill="#fff"/></svg>www.lumavento.dk</li>
    </ul>
  </div>
</section>

<section class="card card--back" aria-label="Visitkort bagside">
  <svg class="card__bands" viewBox="0 0 540 350" aria-hidden="true">
    <polygon points="0,0 232,0 222,22 0,22" fill="var(--purple)"/>
    <polygon points="242,0 540,0 540,22 232,22" fill="var(--pink)"/>
    <polygon points="0,326 330,326 340,310 340,350 0,350" fill="var(--green)"/>
    <polygon points="348,310 540,310 540,350 340,350" fill="var(--orange)"/>
  </svg>

  <div class="back-brand">
    <div class="back-brand__name"><span class="back-brand__dot"></span>lumavento</div>
    <div class="back-brand__rule"></div>
    <p class="back-brand__tagline">Lys til ideer</p>
  </div>
</section>

</body>
</html>
```